interior designer/stylist looking for a letter press business card to reflect the stylish work

Hello Designers,
I need a business card design for an company called Mosaic Interior Design. I'm aiming at the high end residential and private client market in London providing sleek simple interiors. I'd like my business card to be pinterest worthy and expensive looking, i want people to pin it and for it to have a sought after look, and want prospective customers to hire me as their interior designer as my card is so beautiful.
I love letter press design. I also like the use of colour/foil on the edge.
Colour combos & general things I like -
Black and White
Navy Blue and Gold
Neutral colours (muted palette of greys whites navys beiges)
White Marble & brass
Vorelle (fashion designer)
....also open to other suggestions....
Please dont take the pink in the attached photos too literally. i'd like the card to look more masculine than feminine.
I'd like Mosaic on one side in one font, with interior design underneath so one word will make the statement....... unless anyone has any other ideas, open to suggestions.
I'd like a really simple font and for the whole card to look very graphic.
my details -
Petra Wendlecombe
Interior Designer & Stylist
email petra@mosaicinteriordesign.co.uk
phone +447311584209
website wwww.mosaicinteriordesign.co.uk
GO GO GO!! EXCITED TO SEE THE OUTCOME!!
x P
Target Market(s)
High End Residential and private clients
Industry/Entity Type
Business
Contact Information for Business Card
Mosaic Interior Design & Styling
Petra Wendlecombe
phone +447311584209

```html
<!DOCTYPE html>
<html lang="en">
<head>
<meta charset="utf-8">
<title>Mosaic Interior Design – Business Card</title>
<link href="https://fonts.googleapis.com/css2?family=Jost:wght@400;500&display=swap" rel="stylesheet">
<style>
  :root {
    --foil-silver: #c8c8c8;
    --card-white: #ffffff;
    --ink-charcoal: #3f3f40;
  }
  * { margin: 0; padding: 0; box-sizing: border-box; }
  html, body {
    width: 1200px;
    height: 686px;
    overflow: hidden;
    background: var(--foil-silver);
  }
  .card {
    position: relative;
    width: 1200px;
    height: 686px;
    background: var(--foil-silver);
    overflow: hidden;
  }
  .foil-texture {
    position: absolute;
    inset: 0;
    width: 100%;
    height: 100%;
  }
  .card-face {
    position: absolute;
    top: 11px;
    left: 11px;
    right: 11px;
    bottom: 14px;
    background: var(--card-white);
  }
  .wordmark {
    position: absolute;
    left: 0;
    width: 1200px;
    text-align: center;
    color: var(--ink-charcoal);
    font-family: "Jost", "Futura", sans-serif;
    line-height: 1;
    white-space: nowrap;
  }
  .wordmark-name {
    top: 210px;
    font-size: 166px;
    font-weight: 500;
    letter-spacing: 0.045em;
    padding-left: 0.045em;
  }
  .wordmark-tagline {
    top: 388px;
    font-size: 36px;
    font-weight: 400;
    letter-spacing: 0.3em;
    padding-left: 0.3em;
  }
</style>
</head>
<body>
  <div class="card">
    <svg class="foil-texture" viewBox="0 0 1200 686" preserveAspectRatio="none" aria-hidden="true">
      <defs>
        <filter id="foil-grain" x="0" y="0" width="100%" height="100%">
          <feTurbulence type="fractalNoise" baseFrequency="0.9" numOctaves="2" seed="7" result="noise"/>
          <feColorMatrix in="noise" type="matrix"
            values="0 0 0 0 0.86
                    0 0 0 0 0.86
                    0 0 0 0 0.86
                    0 0 0 1.4 -0.45"/>
        </filter>
      </defs>
      <rect width="1200" height="686" fill="#c6c6c6"/>
      <rect width="1200" height="686" filter="url(#foil-grain)"/>
    </svg>

    <div class="card-face"></div>

    <h1 class="wordmark wordmark-name">MOSAIC</h1>
    <p class="wordmark wordmark-tagline">INTERIOR DESIGN</p>
  </div>
</body>
</html>
```